K7 Electrical Services Ltd Web design

I require a web site for my new electrical contracting company. We are customer service orientated. Offering high value electrical installations, design and maintenance. Focused on custom residential and commercial upgrading. Lighting design and application are paramount in our company's services. Industry leading product use and integration are always on the forefront with our customer client services. As well as energy efficiency.

Target Market(s)

Homebuilders, General Contractors, Property management companies, clients, individuals,

Industry/Entity Type

Electric Company

Coding

Coded - Design and coding required

Number of Pages Required

3 page

Requirements
Must have
• Classic, modern, edgy but not trendy . Appeals to the masse.
• 3 page
• home page
• about page
• gallery page
• ability to contact from the webiste
Nice to have
• open to all types of designs that are relative to the construction industry.
• Black, Grey, metallic ice blue and deep purple colours from the logo.
Should not have
• anything cheesy with cartoon light bulb images.

```html
<!DOCTYPE html>
<html lang="en">
<head>
<meta charset="utf-8">
<title>K7 Electrical Services Ltd</title>
<link rel="stylesheet" href="https://fonts.googleapis.com/css2?family=Montserrat:wght@400;600;700;800&family=Open+Sans:wght@400;600&display=swap">
<style>
:root{
  --purple:#6a2d8f;
  --purple-dark:#4b1f68;
  --purple-deep:#3a1752;
  --grey:#8a8a8c;
  --grey-dark:#555558;
  --light:#f2f2f2;
  --line:#d8d8d8;
  --text:#444;
  --white:#fff;
}
*{box-sizing:border-box;margin:0;padding:0}
html,body{width:1200px;height:3236px;overflow:hidden}
body{font-family:"Open Sans",Arial,sans-serif;color:var(--text);background:var(--white);position:relative;font-size:14px}
.h{font-family:"Montserrat",Arial,sans-serif}
section,header,footer{position:absolute;left:0;width:1200px}

/* wordmark */
.brand{display:flex;align-items:center;gap:8px;font-family:"Montserrat",Arial,sans-serif;font-weight:700;color:var(--purple);font-size:18px;letter-spacing:.5px}
.brand .sq{width:14px;height:14px;background:var(--purple)}

/* header */
.site-header{top:0;height:56px;background:var(--white)}
.site-header .brand{position:absolute;left:120px;top:17px}
.header-cta{position:absolute;right:120px;top:6px;font-family:"Montserrat",sans-serif;font-weight:700;font-size:12px;color:var(--purple);letter-spacing:.3px}
.main-nav{position:absolute;right:120px;top:26px;display:flex;gap:4px}
.main-nav a{font-family:"Montserrat",sans-serif;font-size:11px;font-weight:600;color:var(--purple);text-decoration:none;padding:7px 14px}
.main-nav a.active{background:var(--purple);color:var(--white)}

/* hero */
.hero{top:56px;height:544px;background:linear-gradient(115deg,#c9c6c0 0%,#9a958c 30%,#6d6a66 55%,#b79d6c 75%,#e6d9bd 100%)}
.hero-msg{position:absolute;right:150px;top:230px;text-align:right}
.hero-msg span{display:inline-block;font-family:"Montserrat",sans-serif;font-size:28px;line-height:36px;color:var(--white);background:rgba(106,45,143,.55);padding:0 8px;margin-bottom:2px}
.slide-arrow{position:absolute;top:322px;width:22px;height:30px;background:rgba(30,30,30,.7);display:flex;align-items:center;justify-content:center}
.slide-arrow.prev{left:0}.slide-arrow.next{right:0}

/* services band */
.service-band{top:600px;height:200px;display:flex}
.service-half{width:600px;height:200px;padding:24px 0 0;color:var(--white)}
.service-half.residential{background:var(--purple);padding-left:140px}
.service-half.commercial{background:var(--grey);padding-left:180px}
.service-title{display:flex;align-items:center;gap:14px;font-family:"Montserrat",sans-serif;font-size:26px;font-weight:600}
.service-half p{font-size:11.5px;line-height:17px;margin-top:14px;width:300px;opacity:.95}
.badge{position:absolute;left:510px;top:632px;width:180px;height:180px;border-radius:50%;background:var(--white);border:6px solid var(--purple-dark);display:flex;align-items:center;justify-content:center}
.badge .brand{font-size:15px}

/* intro */
.intro{top:800px;height:420px;text-align:center}
.intro .brand{justify-content:center;margin-top:60px;font-size:24px}
.intro-text{width:560px;margin:36px auto 0;font-size:13px;line-height:19px;color:#333}
.feature-row{display:flex;justify-content:center;gap:30px;margin-top:28px}
.feature{width:200px;height:196px;border:1px solid var(--line);padding-top:18px}
.feature .ic{width:86px;height:86px;border-radius:50%;background:var(--purple);margin:0 auto;display:flex;align-items:center;justify-content:center}
.feature h3{font-family:"Montserrat",sans-serif;font-weight:400;font-size:19px;line-height:23px;color:#333;margin-top:16px}

/* about */
.about{top:1270px;height:320px;background:var(--light);text-align:center}
.about-title{display:flex;justify-content:center;align-items:center;gap:10px;margin-top:50px}
.about-title .word{font-family:"Montserrat",sans-serif;font-weight:800;font-size:34px;color:var(--purple)}
.about-title .brand{font-size:22px}
.about p{width:920px;margin:16px auto 0;font-size:11.5px;line-height:17px;color:#444}
.btn{display:inline-block;background:var(--purple);color:var(--white);font-family:"Montserrat",sans-serif;font-weight:600;font-size:16px;padding:10px 26px;margin-top:22px;text-decoration:none}

/* gallery */
.gallery{top:1590px;height:720px}
.section-title{text-align:center;font-family:"Montserrat",sans-serif;font-weight:800;font-size:34px}
.section-title .a{color:var(--purple)}.section-title .b{color:#7c7c7c;font-weight:400}
.gallery .section-title{margin-top:22px}
.rule{width:240px;height:2px;background:var(--line);margin:6px auto 0;position:relative}
.rule::after{content:"";position:absolute;left:90px;width:60px;height:4px;top:-1px;background:var(--purple)}
.tile{position:absolute}
.tile.feature-tile{background:linear-gradient(160deg,#6b4a2a,#2d1d12)}
.tile-overlay{position:absolute;inset:0;background:rgba(74,31,104,.82);color:var(--white);padding:90px 24px 0;text-align:left}
.tile-overlay h4{font-family:"Montserrat",sans-serif;font-size:20px;font-weight:600;text-align:center}
.tile-overlay p{font-size:11px;line-height:16px;margin-top:10px}

/* why */
.why{top:2320px;height:200px;background:var(--light);text-align:center}
.why .section-title{margin-top:24px;font-size:30px}
.why .section-title .a{color:var(--purple)}
.why p{font-family:"Montserrat",sans-serif;font-weight:600;font-size:13px;line-height:19px;color:#333;margin-top:18px}
.why .cta{color:var(--purple);font-weight:700;font-size:12px}

/* contact */
.contact{top:2560px;height:420px}
.contact .section-title{margin-top:24px;font-size:30px}
.contact-form{position:absolute;left:160px;top:140px;width:390px}
.field{height:34px;border:1px solid #bbb;border-radius:3px;margin-bottom:15px;font-size:12px;color:#555;padding:9px 12px}
.field.msg{height:92px}
.submit{display:inline-block;background:var(--purple);color:var(--white);font-family:"Montserrat",sans-serif;font-weight:700;font-size:15px;padding:9px 22px;margin-top:8px}
.contact-info{position:absolute;left:614px;top:145px;width:400px}
.contact-info h3{font-family:"Montserrat",sans-serif;font-weight:800;font-size:22px;color:var(--purple)}
.contact-info p{font-size:13px;color:#333;margin-top:12px;display:flex;align-items:center;gap:6px}
.map{width:400px;height:130px;margin-top:20px;background:linear-gradient(135deg,#e7eae6,#d6ddd6 50%,#e9e6dc);border:1px solid #ccc}

/* footer */
.site-footer{top:3000px;height:236px;background:var(--purple);text-align:center}
.foot-nav{display:flex;justify-content:center;gap:34px;padding-top:22px}
.foot-nav a{color:var(--white);font-family:"Montserrat",sans-serif;font-size:11px;text-decoration:none}
.site-footer .brand{justify-content:center;color:var(--white);font-size:24px;margin-top:30px}
.site-footer .brand .sq{background:var(--white)}
.copyright{position:absolute;left:0;bottom:0;width:1200px;height:56px;background:var(--purple-deep);color:#ddd;font-size:11px;line-height:56px}
</style>
</head>
<body>

<header class="site-header">
  <div class="brand"><span class="sq"></span>K7 Electrical Services</div>
  <div class="header-cta">SCHEDULE YOUR SERVICE TODAY</div>
  <nav class="main-nav">
    <a class="active" href="#">HOME</a><a href="#">ABOUT</a><a href="#">GALLERY</a><a href="#">CONTACT US</a>
  </nav>
</header>

<section class="hero" role="img" aria-label="Photo of an electrician's hands testing a wired panel with a multimeter">
  <div class="hero-msg">
    <span>Offering High Value</span><br>
    <span>Electrical Installations,</span><br>
    <span>Design And Maintenance</span>
  </div>
  <div class="slide-arrow prev"><svg width="10" height="12" viewBox="0 0 10 12"><path d="M7 1 2 6l5 5" stroke="#fff" stroke-width="2" fill="none"/></svg></div>
  <div class="slide-arrow next"><svg width="10" height="12" viewBox="0 0 10 12"><path d="M3 1l5 5-5 5" stroke="#fff" stroke-width="2" fill="none"/></svg></div>
</section>

<section class="service-band">
  <div class="service-half residential">
    <div class="service-title">
      <svg width="42" height="36" viewBox="0 0 42 36"><path d="M3 18 21 3l18 15" stroke="#fff" stroke-width="3" fill="none"/><path d="M9 15v19h24V15" fill="#fff"/><rect x="18" y="23" width="7" height="11" fill="#6a2d8f"/></svg>
      Residential
    </div>
    <p>Custom residential upgrades, new wiring and lighting built around your home, delivered by licensed electricians who care about the details and finish every job clean.</p>
  </div>
  <div class="service-half commercial">
    <div class="service-title">
      <svg width="40" height="38" viewBox="0 0 40 38"><rect x="4" y="4" width="20" height="32" fill="#fff"/><rect x="24" y="14" width="12" height="22" fill="#fff"/><g fill="#8a8a8c"><rect x="8" y="9" width="4" height="4"/><rect x="16" y="9" width="4" height="4"/><rect x="8" y="17" width="4" height="4"/><rect x="16" y="17" width="4" height="4"/><rect x="8" y="25" width="4" height="4"/><rect x="16" y="25" width="4" height="4"/></g></svg>
      Commercial
    </div>
    <p>Commercial installations, service upgrades and maintenance for builders, contractors and property managers, planned to keep your site running safely and on schedule.</p>
  </div>
</section>
<div class="badge"><div class="brand"><span class="sq"></span>K7 Electrical</div></div>

<section class="intro">
  <div class="brand"><span class="sq"></span>K7 Electrical Services</div>
  <p class="intro-text">We are customer service orientated. Offering high value electrical installations, design and maintenance, with industry leading products and a strong focus on energy efficiency since day one.</p>
  <div class="feature-row">
    <div class="feature">
      <div class="ic"><svg width="44" height="44" viewBox="0 0 44 44"><rect x="14" y="4" width="4" height="10" fill="#fff"/><rect x="26" y="4" width="4" height="10" fill="#fff"/><path d="M9 14h26v8a13 13 0 0 1-26 0z" fill="#fff"/><rect x="20" y="34" width="4" height="8" fill="#fff"/></svg></div>
      <h3>Electrical<br>Installations</h3>
    </div>
    <div class="feature">
      <div class="ic"><svg width="44" height="44" viewBox="0 0 44 44"><path d="M8 36 30 14" stroke="#fff" stroke-width="5" stroke-linecap="round"/><circle cx="32" cy="12" r="7" fill="none" stroke="#fff" stroke-width="4"/><path d="M10 8 36 34" stroke="#fff" stroke-width="4" stroke-linecap="round"/><rect x="4" y="4" width="9" height="9" fill="#fff" transform="rotate(45 8.5 8.5)"/></svg></div>
      <h3>Design And<br>Maintenance</h3>
    </div>
    <div class="feature">
      <div class="ic"><svg width="46" height="46" viewBox="0 0 46 46"><circle cx="23" cy="23" r="8" fill="#fff"/><g stroke="#fff" stroke-width="3" stroke-linecap="round"><path d="M23 4v6M23 36v6M4 23h6M36 23h6M10 10l4 4M32 32l4 4M36 10l-4 4M14 32l-4 4"/></g></svg></div>
      <h3>Lighting Design And<br>Application</h3>
    </div>
  </div>
</section>

<section class="about">
  <div class="about-title"><span class="word">ABOUT</span><div class="brand"><span class="sq"></span>K7 Electrical Services</div></div>
  <p>Our team brings years of field experience to every project, from single room lighting updates to complete service upgrades for new commercial builds. We plan carefully, communicate clearly and stand behind our workmanship with honest pricing and reliable scheduling for every client we serve.</p>
  <p>We work alongside homebuilders, general contractors and property management companies to deliver installations that meet code, look great and save energy. Lighting design is at the heart of what we do, and we integrate modern controls and efficient fixtures to suit each space and each budget perfectly.</p>
  <a class="btn" href="#">Call Us Today</a>
</section>

<section class="gallery">
  <h2 class="section-title"><span class="a">WORK</span> <span class="b">GALLERY</span></h2>
  <div class="rule"></div>
  <div class="tile feature-tile" style="left:140px;top:182px;width:340px;height:266px" role="img" aria-label="Photo of an electrical installation">
    <div class="tile-overlay">
      <h4>Electrical<br>Installations</h4>
      <p>Panel upgrades, new circuits and full rewiring completed to code, tested and documented for every home and commercial site we power.</p>
    </div>
  </div>
  <div class="tile" style="left:488px;top:182px;width:224px;height:130px;background:linear-gradient(135deg,#d8cfc4,#a99a88)" role="img" aria-label="Photo of hands connecting wires"></div>
  <div class="tile" style="left:720px;top:182px;width:340px;height:130px;background:linear-gradient(135deg,#e8e2d6,#b9ad98)" role="img" aria-label="Photo of an electrician working on a ceiling fixture"></div>
  <div class="tile" style="left:488px;top:318px;width:108px;height:130px;background:linear-gradient(135deg,#9a7a52,#4a3a28)" role="img" aria-label="Photo of wiring in a junction box"></div>
  <div class="tile" style="left:604px;top:318px;width:108px;height:130px;background:linear-gradient(135deg,#c9b08a,#7a5e3c)" role="img" aria-label="Photo of installed light fixtures"></div>
  <div class="tile" style="left:720px;top:318px;width:340px;height:130px;background:linear-gradient(135deg,#d7c3a3,#8c6f4a)" role="img" aria-label="Photo of an electrician installing a ceiling light"></div>
  <div class="tile" style="left:140px;top:456px;width:340px;height:176px;background:linear-gradient(135deg,#c58a3a,#5b4a3a)" role="img" aria-label="Photo of a multimeter testing a circuit"></div>
  <div class="tile" style="left:488px;top:456px;width:150px;height:176px;background:linear-gradient(135deg,#7d8a96,#3c4650)" role="img" aria-label="Photo of an electrician at a panel"></div>
  <div class="tile" style="left:646px;top:456px;width:414px;height:176px;background:linear-gradient(135deg,#e0b070,#7a4a22)" role="img" aria-label="Photo of a warmly lit interior with designed lighting"></div>
</section>

<section class="why">
  <h2 class="section-title"><span class="a">WHY CHOOSE</span> <span class="b">US</span></h2>
  <p>Lighting design and application are paramount in our company's services.<br>Industry leading product use &amp; integration are always on the forefront with our customer client services.<br><span class="cta">SCHEDULE YOUR SERVICE TODAY</span></p>
</section>

<section class="contact">
  <h2 class="section-title"><span class="a">GET IN</span> <span class="b">TOUCH</span></h2>
  <div class="rule"></div>
  <form class="contact-form">
    <div class="field">Name*</div>
    <div class="field">Phone</div>
    <div class="field">Email*</div>
    <div class="field msg">Message*</div>
    <span class="submit">SUBMIT</span>
  </form>
  <div class="contact-info">
    <h3>SCHEDULE YOUR SERVICE TODAY</h3>
    <p>CALL US : 555-014-2387</p>
    <p>OUR OFFICE: Street Name, City Name State Zipcode</p>
    <div class="map" role="img" aria-label="Map showing the office location"></div>
  </div>
</section>

<footer class="site-footer">
  <nav class="foot-nav"><a href="#">HOME</a><a href="#">ABOUT</a><a href="#">GALLERY</a><a href="#">CONTACT US</a></nav>
  <div class="brand"><span class="sq"></span>K7 Electrical Services</div>
  <div class="copyright">Copyright © 2016 K7 Electrical Services Ltd. All Rights Reserved</div>
</footer>

</body>
</html>
```